Business card design for Virtual Assistance company

I need a business card designed for my virtual assistance company. We are a small company who services primarily C-level executive clients. The card needs to be double sided with the following contact information on the back:
Melissa Thornbury
Owner/CEO
info@rkpadvisory.net
www.rkpadvisory.net
555.302.9817

The front side should just have the company name incorporated: "RKP Advisory" and "virtual assistance"

The card should be simplistic, but eye catching and should speak to high level executives. Our primary focus areas consist of executive assistance and government contracting.

Target Market(s)

CEOs and executives

Contact Information for Business Card

see project description. phone, email, website.

Colors

Designer to choose only greyscale colors for use in the design.

```html
<!DOCTYPE html>
<html lang="en">
<head>
<meta charset="utf-8">
<title>RKP Advisory – Business Card</title>
<link href="https://fonts.googleapis.com/css2?family=EB+Garamond:wght@400;700&family=Montserrat:wght@400&display=swap" rel="stylesheet">
<style>
  :root {
    --bg: #ececec;
    --card-white: #ffffff;
    --ink: #1c1c1c;
    --mark-grey: #333333;
    --card-black: #141414;
    --pattern-light: #3a3a3a;
    --pattern-dark: #0e0e0e;
    --white: #ffffff;
  }
  * { margin: 0; padding: 0; box-sizing: border-box; }
  html, body {
    width: 1200px; height: 1108px; overflow: hidden;
    background: var(--bg);
  }
  .canvas { position: relative; width: 1200px; height: 1108px; }

  .card { position: absolute; }
  .card--front {
    left: 219px; top: 51px; width: 774px; height: 472px;
    background: var(--card-white);
  }
  .card--back {
    left: 217px; top: 569px; width: 777px; height: 456px;
    background: var(--card-black);
  }

  .brand {
    position: absolute; left: 37px; top: 62px;
    font-family: "EB Garamond", serif; color: var(--ink);
    text-align: center;
  }
  .brand__name { font-size: 42px; font-weight: 400; line-height: 1; letter-spacing: -0.5px; }
  .brand__tagline { font-size: 19px; font-weight: 400; letter-spacing: 0.3px; margin-top: 10px; }

  .person { position: absolute; left: 30px; top: 250px; color: var(--ink); }
  .person__name { font-family: "EB Garamond", serif; font-weight: 700; font-size: 29px; line-height: 1; }
  .person__title { font-family: Montserrat, sans-serif; font-size: 17px; margin-top: 7px; }

  .contacts { position: absolute; left: 30px; top: 351px; list-style: none;
    font-family: Montserrat, sans-serif; font-size: 17px; color: var(--ink); }
  .contacts li { display: flex; align-items: center; height: 31px; }
  .contacts svg { width: 17px; height: 17px; margin-right: 9px; fill: var(--ink); }

  .wordmark {
    position: absolute; left: 380px; top: 200px; width: 350px;
    text-align: center; font-family: "EB Garamond", serif; font-weight: 400;
    font-size: 60px; line-height: 1; color: var(--mark-grey);
  }

  .pattern {
    position: absolute; inset: 0;
    background: linear-gradient(100deg, var(--pattern-light) 0%, #222 40%, var(--pattern-dark) 100%);
  }
  .wordmark--back {
    position: absolute; right: 60px; bottom: 92px;
    font-family: "EB Garamond", serif; font-weight: 400;
    font-size: 34px; line-height: 1; color: var(--white);
  }
</style>
</head>
<body>
<main class="canvas">
  <section class="card card--front" aria-label="Business card front">
    <div class="brand">
      <div class="brand__name">RKP Advisory</div>
      <div class="brand__tagline">VIRTUAL ASSISTANCE</div>
    </div>

    <div class="person">
      <div class="person__name">Melissa Thornbury</div>
      <div class="person__title">Owner/CEO</div>
    </div>

    <ul class="contacts">
      <li>
        <svg viewBox="0 0 24 24" aria-hidden="true"><path d="M6.6 10.8a15.1 15.1 0 0 0 6.6 6.6l2.2-2.2c.3-.3.7-.4 1-.2 1.1.4 2.3.6 3.6.6.6 0 1 .4 1 1V20c0 .6-.4 1-1 1A17 17 0 0 1 3 4c0-.6.4-1 1-1h3.5c.6 0 1 .4 1 1 0 1.3.2 2.5.6 3.6.1.3 0 .7-.2 1z"/></svg>
        555.302.9817
      </li>
      <li>
        <svg viewBox="0 0 24 24" aria-hidden="true"><path d="M3 6h18v12H3z" fill="none"/><path d="M3 6.5 12 12l9-5.5V18H3z"/><path d="M3 5h18v.8L12 11 3 5.8z"/></svg>
        info@rkpadvisory.net
      </li>
      <li>
        <svg viewBox="0 0 24 24" aria-hidden="true"><circle cx="12" cy="12" r="9.5"/><path d="M12 2.5v19M2.5 12h19M12 2.5c-3 3-3 16 0 19M12 2.5c3 3 3 16 0 19" stroke="#fff" stroke-width="1.2" fill="none"/></svg>
        www.rkpadvisory.net
      </li>
    </ul>

    <div class="wordmark">RKP Advisory</div>
  </section>

  <section class="card card--back" aria-label="Business card back">
    <div class="pattern" role="img" aria-label="Repeating tonal brand pattern on black, fading from grey at left to black at right"></div>
    <div class="wordmark--back">RKP Advisory</div>
  </section>
</main>
</body>
</html>
```